Upmarket Dessert Lounge needs a Business Card Design

We are an upmarket dessert lounge needing a business card to match our image.

We want something that is simple yet beautiful, feminine, classy, sophisticated and elegant. We want it to stand out and don't mind if it is bold.

The design should include our logo and colours of red or maroon with gold highlights. We don't mind if black is used.

Marlow & Quince

Target Market(s)

For those who like to indulge or treat themselves and give in to their temptations on good quality desserts.

Industry/Entity Type

Business

Requirements
Must have
• Must include our logo and our name

Marlow & Quince

M & Q

```html
<!DOCTYPE html>
<html lang="en">
<head>
<meta charset="utf-8">
<title>Marlow &amp; Quince — Business Card</title>
<link rel="stylesheet" href="https://fonts.googleapis.com/css2?family=Libre+Baskerville:wght@400;700&family=Open+Sans:wght@400;600&display=swap">
<style>
  :root {
    --maroon: #7a1518;
    --maroon-deep: #5e0e11;
    --cream: #f6d29c;
    --gold: #e9bf7e;
    --ink: #2b2b2b;
    --paper: #ffffff;
    --backdrop: #ece7e1;
  }
  * { box-sizing: border-box; margin: 0; padding: 0; }
  html, body {
    width: 1200px; height: 758px; overflow: hidden;
    background: var(--backdrop);
    font-family: "Open Sans", Arial, sans-serif;
    color: var(--ink);
  }
  .stage { position: relative; width: 1200px; height: 758px; }
  .card {
    position: absolute;
    width: 540px; height: 310px;
    background: var(--paper);
    border-radius: 24px;
    overflow: hidden;
    box-shadow: 0 10px 26px rgba(60, 40, 30, 0.22);
  }
  .card--front { left: 45px; top: 224px; }
  .card--back { left: 615px; top: 224px; }

  /* front */
  .brand-mark {
    position: absolute; left: 36px; top: 34px;
    display: flex; align-items: center; gap: 10px;
  }
  .brand-mark__dot {
    width: 16px; height: 16px; border-radius: 50%;
    background: var(--maroon);
  }
  .brand-mark__name {
    font-family: "Libre Baskerville", Georgia, serif;
    font-weight: 400; font-size: 25px; letter-spacing: 1px;
    color: var(--maroon);
    text-transform: uppercase;
  }
  .address {
    position: absolute; left: 36px; top: 134px;
    font-size: 13px; letter-spacing: 0.3px;
  }
  .contact-list {
    position: absolute; left: 36px; top: 170px;
    list-style: none; font-size: 12px; line-height: 18px;
  }
  .contact-list li { display: flex; align-items: center; gap: 6px; }
  .contact-list svg { width: 11px; height: 11px; fill: var(--ink); }
  .person {
    position: absolute; right: 40px; top: 112px; text-align: right;
  }
  .person__name {
    font-family: "Libre Baskerville", Georgia, serif;
    font-weight: 700; font-size: 17px; letter-spacing: 0.8px;
  }
  .person__title { font-size: 12px; margin-top: 1px; }
  .wave { position: absolute; left: 0; bottom: 0; width: 540px; height: 130px; }
  .wave__cream { fill: var(--cream); }
  .wave__maroon { fill: var(--maroon); }
  .front-web {
    position: absolute; right: 30px; bottom: 16px;
    color: var(--paper); font-size: 13px; letter-spacing: 0.6px;
  }

  /* back */
  .monogram {
    position: absolute; left: 50%; top: 52px; transform: translateX(-50%);
    width: 210px; height: 150px; border-radius: 50%;
    background: var(--maroon);
    display: flex; align-items: center; justify-content: center;
  }
  .monogram__letters {
    font-family: "Libre Baskerville", Georgia, serif;
    font-weight: 400; font-size: 52px; color: var(--cream);
  }
  .back-web {
    position: absolute; left: 0; right: 0; top: 236px; text-align: center;
    font-size: 19px; letter-spacing: 3px; color: var(--ink);
  }
</style>
</head>
<body>
<main class="stage">
  <section class="card card--front" aria-label="Business card front">
    <div class="brand-mark">
      <span class="brand-mark__dot"></span>
      <span class="brand-mark__name">Marlow &amp; Quince</span>
    </div>
    <p class="address">Street Name, City Name, State Zip Code</p>
    <ul class="contact-list">
      <li>
        <svg viewBox="0 0 24 24" aria-hidden="true"><path d="M6.6 10.8a15 15 0 0 0 6.6 6.6l2.2-2.2a1 1 0 0 1 1-.25 11.4 11.4 0 0 0 3.6.57 1 1 0 0 1 1 1V20a1 1 0 0 1-1 1A17 17 0 0 1 3 4a1 1 0 0 1 1-1h3.5a1 1 0 0 1 1 1c0 1.25.2 2.45.57 3.57a1 1 0 0 1-.25 1z"/></svg>
        987-654-3210
      </li>
      <li>
        <svg viewBox="0 0 24 24" aria-hidden="true"><path d="M7 1h10a2 2 0 0 1 2 2v18a2 2 0 0 1-2 2H7a2 2 0 0 1-2-2V3a2 2 0 0 1 2-2zm0 4v12h10V5zm5 14a1 1 0 1 0 0 2 1 1 0 0 0 0-2z"/></svg>
        987-654-3210
      </li>
      <li>
        <svg viewBox="0 0 24 24" aria-hidden="true"><path d="M2 5h20v14H2zm2 2v.5l8 5 8-5V7z"/></svg>
        info@marlowquince.com
      </li>
    </ul>
    <div class="person">
      <p class="person__name">Your name</p>
      <p class="person__title">Title</p>
    </div>
    <svg class="wave" viewBox="0 0 540 130" preserveAspectRatio="none" aria-hidden="true">
      <path class="wave__cream" d="M0,82 C150,125 330,64 540,14 L540,130 L0,130 Z"/>
      <path class="wave__maroon" d="M0,100 C160,135 340,80 540,30 L540,130 L0,130 Z"/>
    </svg>
    <p class="front-web">www.marlowquince.com</p>
  </section>

  <section class="card card--back" aria-label="Business card back">
    <div class="monogram">
      <span class="monogram__letters">M &amp; Q</span>
    </div>
    <p class="back-web">www.marlowquince.com</p>
  </section>
</main>
</body>
</html>
```